Why engage Insight Harbor?

We are starting a new company that will perform usability consulting and offer usability lab rental. We are in need a one page description flyer.
Updates

Wow! We saw some very interesting and creative flyers posted for review in our contest.

Unfortunately, my schedule became a bit crazy and I may not get back to evaluating them until next week :(  In the meantime, I did want to say thank you for your entries!

Cheers!
Marla

Target Market(s)

product designers, human factors/usability researchers, consumer researcher firms, etc

Industry/Entity Type

It Company

Requirements
Must have
• We would like to see designs with a simple, yet modern, sophisticated feel. I will include our logo images that need to be incorporated along with the font used.

The file called flyer.pdf has all of the information that needs to be included.

Please include 1-3 appropriate stock photos. Please see text in flyer.pdf for description of our services.

Nice to have
• Additionally, there is a sample flyer design that we like for reference. Not a requirement...it is just a reference for the kind of style that we are looking for.

```html
<!DOCTYPE html>
<html lang="en">
<head>
<meta charset="utf-8">
<title>Why Engage Insight Harbor?</title>
<link rel="stylesheet" href="https://fonts.googleapis.com/css2?family=Raleway:wght@500&family=Source+Sans+3:wght@400;600;700&family=Oswald:wght@600&display=swap">
<style>
  :root {
    --navy: #1c3360;
    --green: #8dc63f;
    --green-dark: #79b12e;
    --panel: #e4efd4;
    --rule: #9aa48e;
    --ink: #1d1d1d;
    --white: #ffffff;
  }
  * { box-sizing: border-box; margin: 0; padding: 0; }
  html, body { width: 927px; height: 1200px; overflow: hidden; background: var(--white); }
  body { font-family: "Source Sans 3", Arial, sans-serif; color: var(--ink); position: relative; }

  .hero-photo {
    position: absolute; left: 0; top: 0; width: 462px; height: 348px;
    background: linear-gradient(160deg, #3a3f47 0%, #1b1e24 45%, #3d6b8a 70%, #2f5d2c 100%);
  }
  .shoppers-photo {
    position: absolute; left: 462px; top: 0; width: 465px; height: 205px;
    background: radial-gradient(circle at 45% 40%, #d9363b 0 10%, #f4efe8 11% 100%);
  }
  .shoppers-photo::after {
    content: ""; position: absolute; inset: 0;
    background: linear-gradient(90deg, rgba(240,140,40,.35), rgba(255,255,255,0) 40%, rgba(240,140,40,.35));
  }

  .brand { position: absolute; left: 462px; top: 205px; width: 465px; height: 143px; padding: 28px 0 0 20px; }
  .brand-name {
    display: flex; align-items: center; gap: 14px;
    font-family: "Raleway", Arial, sans-serif; font-weight: 500;
    font-size: 44px; letter-spacing: 1px; color: var(--navy); line-height: 1;
  }
  .brand-mark { width: 30px; height: 30px; border-radius: 50%; background: var(--green); flex: none; }
  .brand-address { margin-top: 24px; font-weight: 700; font-size: 16px; color: var(--ink); }

  .intro-band {
    position: absolute; left: 0; top: 348px; width: 927px; height: 136px;
    background: var(--navy); color: var(--white);
    display: grid; grid-template-columns: 1fr 1fr; column-gap: 30px;
    padding: 16px 18px 0 18px; font-size: 16.5px; line-height: 1.22;
  }

  .reasons {
    position: absolute; left: 15px; top: 487px; width: 896px; height: 643px;
    border: 3px solid var(--green); border-radius: 26px; background: var(--white);
    overflow: hidden; display: flex;
  }
  .reasons-title {
    width: 90px; flex: none; position: relative;
  }
  .reasons-title span {
    position: absolute; left: 50%; top: 50%; transform: translate(-50%, -50%) rotate(-90deg);
    white-space: nowrap; color: var(--green); font-weight: 600; font-size: 31px; letter-spacing: 2px;
  }
  .reasons-title::before {
    content: ""; position: absolute; left: 16px; top: 0; bottom: 0; width: 48px; background: var(--green);
  }
  .reasons-title span { color: var(--white); z-index: 1; }
  .reason-list {
    flex: 1; background: var(--panel); list-style: none; padding: 12px 18px 0 14px;
  }
  .reason {
    display: grid; grid-template-columns: 162px 1fr; column-gap: 0;
    border-bottom: 1px solid var(--rule); padding: 8px 0 8px 0;
  }
  .reason:last-child { border-bottom: none; }
  .reason-label { color: var(--green-dark); font-weight: 600; font-size: 17.5px; line-height: 1.1; }
  .reason-text { font-weight: 600; font-size: 12.6px; line-height: 1.42; padding-right: 6px; }
  .reason.tight .reason-text { padding-right: 130px; }

  .call-badge {
    position: absolute; left: 758px; top: 960px; width: 168px; height: 168px; border-radius: 50%;
    background: var(--green); border: 5px solid var(--white);
    display: flex; flex-direction: column; align-items: center; justify-content: center;
    font-family: "Oswald", Arial, sans-serif; color: var(--white); line-height: .95;
    transform: rotate(-10deg);
  }
  .call-badge .small { font-size: 36px; }
  .call-badge .big { font-size: 56px; }

  .contact-band {
    position: absolute; left: 0; top: 1139px; width: 927px; height: 61px; background: var(--navy);
    color: var(--white); display: flex; align-items: center; padding-left: 66px; gap: 70px;
    font-weight: 600; font-size: 26px; letter-spacing: .5px;
  }
  .contact-phone { display: flex; align-items: center; gap: 10px; }
  .contact-phone svg { width: 22px; height: 26px; }
</style>
</head>
<body>
  <div class="hero-photo" role="img" aria-label="Photo: researchers looking down into an open dollhouse with people in its rooms"></div>
  <div class="shoppers-photo" role="img" aria-label="Illustration: orange figures with shopping carts and one figure on a red target"></div>

  <header class="brand">
    <div class="brand-name"><span class="brand-mark"></span>INSIGHT HARBOR</div>
    <p class="brand-address">2140 W. Lantern Bay Road, Tempe AZ 85281</p>
  </header>

  <section class="intro-band">
    <p>We are a network of human factors engineers, usability specialists, and cognitive/consumer psychologists, who help you design and evaluate the usefulness, usability and desirability of your products.</p>
    <p>Lease our state of the art consumer research and usability lab, or partner with us on usability testing, eyetracking studies, participatory design, online survey research, ethnographic studies, focus groups and more.</p>
  </section>

  <section class="reasons">
    <div class="reasons-title"><span>WHY ENGAGE INSIGHT HARBOR?</span></div>
    <ul class="reason-list">
      <li class="reason"><h3 class="reason-label">Experience</h3><p class="reason-text">Founded by a Professor of Cognitive Psychology and Human Factors with over twenty years of experience, our group includes MS and PhD level consultants with experience working for and consulting with companies like Northwind, Brightline, Corvale Medical, Pulsera, Mesa Valley Hospitals, Hale and Morrow, Veritek, and Starlane Studios.</p></li>
      <li class="reason"><h3 class="reason-label">Service</h3><p class="reason-text">Full range of consumer research and usability services, including ethnography, participatory design, questionnaires, user diaries, usability testing, usability evaluation, card sorting, psychometric scaling, focus groups and more.</p></li>
      <li class="reason"><h3 class="reason-label">Range of products and industries</h3><p class="reason-text">Our consultants have extensive experience in design and evaluation of computing, web, tablet, smart phone, product, medical, consumer, and many other types of products and user interfaces.</p></li>
      <li class="reason"><h3 class="reason-label">Client Service Specialist</h3><p class="reason-text">Need copies, printing, lunch, or dinner reservations? Our client service specialist will make sure you have everything you need.</p></li>
      <li class="reason"><h3 class="reason-label">Recruiting</h3><p class="reason-text">Sizable database with ability to recruit research participants according to age, sex, occupation, health status, and other parameters.</p></li>
      <li class="reason"><h3 class="reason-label">Onsite or remote streaming video</h3><p class="reason-text">Sessions can be viewed in many ways: Through our observation mirror, in our meeting room via pan-tilt-zoom camera, at your site on your computer, on your tablet or phone.</p></li>
      <li class="reason"><h3 class="reason-label">Audio/video</h3><p class="reason-text">On-site video editing. Highlight video included in facility rental.</p></li>
      <li class="reason"><h3 class="reason-label">Office space</h3><p class="reason-text">Meeting room for work, phone calls and conference calls. Wireless Internet.</p></li>
      <li class="reason tight"><h3 class="reason-label">Accessibility</h3><p class="reason-text">Located on the first floor, with ample, free, convenient and handicap parking. Adjustable artificial and natural lighting.</p></li>
      <li class="reason tight"><h3 class="reason-label">Transcription</h3><p class="reason-text">Transcription services and word frequency key-words-in-context, and word co-occurrence analyses available</p></li>
      <li class="reason tight"><h3 class="reason-label">Bilingual</h3><p class="reason-text">Several consultants fluent in both English and Spanish</p></li>
    </ul>
  </section>

  <div class="call-badge"><span class="small">CALL US</span><span class="big">NOW</span></div>

  <footer class="contact-band">
    <span class="contact-phone">
      <svg viewBox="0 0 22 26" aria-hidden="true"><path d="M5 1 L9 1 L10 7 L7 9 Q9 15 13 18 L16 15 L21 17 L21 22 Q19 25 15 24 Q3 19 1 6 Q1 2 5 1 Z" fill="#fff"/></svg>
      480.555.0147
    </span>
    <span class="contact-web">WWW.INSIGHT-HARBOR.COM</span>
  </footer>
</body>
</html>
```